4 panel (or page) brochure

We need a brochure design for a Oklahoma based company. We manufacture and sell underground and below ground shelters. We sell our shelters in our local showroom, as well distribute our shelters to a big box national retailer. I would like to have a simple design that includes a few pictures of our product and details on each product we offer as well as install details for each product. Our out of state retailers likely will not have our product display so we will need something that sells the product without seeing it in person.

I would like something that it easily printable as well as able to edit at a later time if needed.

I've included Catalog/Brochure Copy
Pictures of Below Ground Units/Above Ground Units - feel free to edit or touch up.
Some brochure ideas I found on Draftwell that seemed to be similar to what we can do.
The Inside of a brochure we did a while back that we liked (style-wise)
A general info flyer for more information

It Company

```html
<!DOCTYPE html>
<html lang="en">
<head>
<meta charset="utf-8">
<title>StormHold Brochure – Above Ground Safe Rooms</title>
<link href="https://fonts.googleapis.com/css2?family=Montserrat:wght@300;400;500;600;700&display=swap" rel="stylesheet">
<style>
:root{
  --red:#d01f26;
  --red-dark:#b3161c;
  --ink:#555555;
  --ink-dark:#3a3a3a;
  --rule:#cfcfcf;
  --table-head:#bdbdbd;
  --table-row:#ececec;
  --page:#ffffff;
  --canvas:#ffffff;
}
*{box-sizing:border-box;margin:0;padding:0}
html,body{width:1200px;height:900px;overflow:hidden;background:var(--canvas)}
body{font-family:"Montserrat",Arial,sans-serif;color:var(--ink);position:relative}
.page{position:absolute;top:55px;height:790px;background:var(--page);border:1px solid var(--rule)}
.page--left{left:42px;width:557px}
.page--right{left:599px;width:559px}
.abs{position:absolute}

.header-band{left:0;top:38px;width:525px;height:60px}
.header-title{right:56px;top:52px;text-align:right;color:#fff;line-height:1}
.header-title .strong{font-weight:700;font-size:16px;letter-spacing:.3px;display:flex;align-items:center;gap:6px;justify-content:flex-end}
.header-title .strong i{display:inline-block;width:10px;height:10px;background:#fff}
.header-title .light{font-weight:300;font-size:16px;margin-top:3px;letter-spacing:.4px}

.product-shot{left:20px;top:116px;width:178px;height:190px;background:linear-gradient(180deg,#f2f2f2,#e2e2e2 80%,#fafafa)}

.intro{left:212px;top:116px;width:312px;font-size:7.6px;line-height:13px}
h3.section{font-size:7.6px;font-weight:700;color:var(--red);letter-spacing:.2px;text-transform:uppercase}
.features-head{left:212px;top:219px}
ul.bullets{list-style:none;font-size:7.6px;line-height:12.2px}
ul.bullets li{padding-left:8px;position:relative;margin-bottom:1.5px}
ul.bullets li::before{content:"•";position:absolute;left:0}
.features-a{left:212px;top:233px;width:150px}
.features-b{left:375px;top:233px;width:150px}
.features-b li.cont{padding-left:8px}
.features-b li.cont::before{content:""}

.types-head{left:34px;top:319px}
table{border-collapse:collapse;font-size:7.4px}
.sizes{left:34px;top:334px;width:155px}
.sizes th{background:var(--table-head);color:var(--ink-dark);font-weight:600;height:13px}
.sizes td{text-align:center;height:14px;border-bottom:1px solid #fff}
.sizes tr:nth-child(even) td{background:var(--table-row)}
.sizes tr:nth-child(odd) td{background:#f7f7f7}
.sizes tr:last-child td{background:var(--table-head);color:#fff}

.install-head{left:34px;top:445px}
.install-list{left:34px;top:459px;width:150px}

.benefits-head{left:212px;top:391px}
.benefits-list{left:212px;top:405px;width:312px}

.custom-head{left:212px;top:495px}
.custom{left:212px;top:511px;width:312px}
.custom th{background:var(--table-head);color:var(--ink-dark);font-weight:600;height:12px;border-right:1px solid #fff}
.custom td{background:#f1f1f1;vertical-align:top;line-height:10px;padding:2px 5px;border-right:1px solid #fff}
.custom td.loc{text-align:center;padding:1px 0;height:12px}
.custom td.loc.hl{background:#dcdcdc}

.brand{display:flex;align-items:center;gap:6px;color:var(--red);font-weight:700}
.brand i{display:inline-block;background:var(--red)}
.brand--small{left:238px;top:624px;font-size:13px}
.brand--small i{width:9px;height:9px}
.brand--large{left:392px;top:218px;font-size:19px}
.brand--large i{width:12px;height:12px}

.phone{left:213px;top:679px;font-size:7px}
.phone b,.email b{font-size:13px;font-weight:600;color:var(--ink-dark);margin-left:5px}
.email{left:187px;top:697px;font-size:7px}

.visit{left:34px;top:753px;font-size:7.4px}
.office{font-size:7.2px;line-height:9.5px}
.office b{display:block;color:var(--red);font-weight:700}
.office-okc{left:134px;top:740px}
.office-tulsa{left:248px;top:743px}
.site{left:410px;top:752px;font-size:9px;font-weight:700;color:var(--red);letter-spacing:.3px}

.photo{position:absolute}
.photo--storm{left:0;top:279px;width:178px;height:418px;background:linear-gradient(180deg,#6b6f74,#9aa0a6 45%,#55585c)}
.photo--hatch{left:187px;top:279px;width:372px;height:196px;background:linear-gradient(135deg,#b9b9b9,#d6d6d6 50%,#9c9c9c)}
.photo--family{left:187px;top:483px;width:238px;height:214px;background:linear-gradient(180deg,#e9e4de,#d9c7b5 60%,#f1f1f1)}
.photo--stairs{left:434px;top:483px;width:125px;height:214px;background:linear-gradient(180deg,#f0f0f0 30%,#4a4a4a 60%,#2e2e2e)}

.cover-band{left:0;top:707px;width:559px;height:83px;background:var(--red)}
.cover-title{right:36px;top:718px;text-align:right;color:#fff;line-height:1}
.cover-title .strong{font-size:27px;font-weight:700;letter-spacing:.5px}
.cover-title .light{font-size:15px;font-weight:300;letter-spacing:.8px;margin-top:3px}
</style>
</head>
<body>

<section class="page page--left">
  <svg class="abs header-band" viewBox="0 0 525 60" width="525" height="60" aria-hidden="true">
    <polygon points="0,0 495,0 525,30 525,60 0,60" fill="var(--red)"/>
  </svg>
  <div class="abs header-title">
    <div class="strong"><i></i>ABOVE GROUND</div>
    <div class="light">SAFE ROOMS</div>
  </div>

  <div class="abs product-shot" role="img" aria-label="White steel above ground safe room with front door and lookout window"></div>

  <p class="abs intro">Our above ground shelters are engineered, tested and meet the highest quality standards at a competitive price.&nbsp; Our shelters come in a variety of sizes ranging from 3-4 people to 16-20 people. Our above ground shelters are built stronger than our competitors using a minimum of 3/16” steel, are fully painted inside and out and are made to withstand 260 mph winds. All units also come standard with a &nbsp;bullet proof lookout glass window. Our safe rooms are FEMA compliant and are built using FEMA publications 320 guidelines.</p>

  <h3 class="abs section features-head">Technical Features</h3>
  <ul class="abs bullets features-a">
    <li>3/16” steel plates for exterior skin</li>
    <li>Solid welds</li>
    <li>2” × 2” × ¼” square tubing for internal subframe</li>
    <li>3” × 3” × ¼” angle iron for bottom frame</li>
    <li>8” custom designed air vents</li>
    <li>3 BHMA/ANSI Grade 1 Dead bolt locking system</li>
    <li>Concrete anchoring system</li>
    <li>Bullet proof window comes standard</li>
  </ul>
  <ul class="abs bullets features-b">
    <li class="cont">with every shelter</li>
    <li>Double-skinned door (3/16” exterior plate and 12 gauge interior sheet</li>
    <li>3 heavy duty removable steel door hinges</li>
    <li>24” wide door</li>
    <li>Door opens to the inside to keep debris from blocking door</li>
    <li>Door is removable in case of emergency</li>
  </ul>

  <h3 class="abs section types-head">Types &amp; Sizes</h3>
  <table class="abs sizes">
    <thead><tr><th>Size</th><th>Fits</th></tr></thead>
    <tbody>
      <tr><td>3' × 5' or 4' × 4'</td><td>2-4 people</td></tr>
      <tr><td>4' × 6'</td><td>4-6 people</td></tr>
      <tr><td>4' × 8'</td><td>6-8 people</td></tr>
      <tr><td>5' × 7'</td><td>8-10 people</td></tr>
    </tbody>
  </table>

  <h3 class="abs section install-head">Installation Process</h3>
  <ul class="abs bullets install-list">
    <li>Shelter is placed with an excavator and bolted to concrete with 4 ¾ inch bolts</li>
    <li>Can be installed outside on a concrete slab of at least 15”-20”</li>
  </ul>

  <h3 class="abs section benefits-head">Additional Benefits</h3>
  <ul class="abs bullets benefits-list">
    <li>Our above ground units have a 36” side door, flat to the ground, which means they are wide enough and flat enough to be wheel chair accessible.</li>
    <li>Our above ground units are typically installed in about 2 hours.</li>
    <li>A variety of sizes to suit your need</li>
    <li>All units come standard with a bulletproof lookout glass</li>
    <li>Can also be used as a panic room</li>
  </ul>

  <h3 class="abs section custom-head">Customization Options</h3>
  <table class="abs custom">
    <thead><tr><th>Door location</th><th>Door opening</th><th>Door hinges</th></tr></thead>
    <tbody>
      <tr><td class="loc">End Door (Short Side)</td><td rowspan="3">Choice of door opening to the outside or inside of shelter</td><td rowspan="3">Hinges can be placed on right side or left side of door</td></tr>
      <tr><td class="loc hl">Side Door (Long Side Right)</td></tr>
      <tr><td class="loc">Side Door (Long Side Left)</td></tr>
    </tbody>
  </table>

  <div class="abs brand brand--small"><i></i>STORMHOLD</div>

  <div class="abs phone">Phone<b>(405) 555-0142</b></div>
  <div class="abs email">E-mail<b>info@stormhold.com</b></div>

  <div class="abs visit">Visit our showroom at</div>
  <div class="abs office office-okc"><b>OKLAHOMA</b>4200 S. Meridian Ave.<br>Oklahoma City, OK 73119<br>(405) 555-0142</div>
  <div class="abs office office-tulsa"><b>TULSA</b>2250 E. Harvard Ave Tulsa,<br>OK 74114 (918) 555-0188</div>
  <div class="abs site">STORMHOLD.COM</div>
</section>

<section class="page page--right">
  <div class="abs brand brand--large"><i></i>STORMHOLD</div>

  <div class="photo photo--storm" role="img" aria-label="Tornado funnel and lightning over an empty highway"></div>
  <div class="photo photo--hatch" role="img" aria-label="Open steel hatch of an underground shelter set in a concrete garage floor"></div>
  <div class="photo photo--family" role="img" aria-label="Smiling family of four in white shirts"></div>
  <div class="photo photo--stairs" role="img" aria-label="Carpeted steps leading down into the shelter"></div>

  <div class="abs cover-band"></div>
  <div class="abs cover-title">
    <div class="strong">SAFE AND SOUND</div>
    <div class="light">UNDERGROUND</div>
  </div>
</section>

</body>
</html>
```